Cruise Booking Website

Cruise search and booking website

This project is a redesign of a cruise booking website we did a few years ago.

The current website is located here: http://voyage.pylonworks.example/en/

It's not fully functional but gives you ad idea how miserable the old design was.

All the information about cruises, cruise lines, destinations, ports and shore excursions will be similar to http://www.sailquest.example/
Actual search pages (form, results, single result, sailing and cabin selection, ship info, booking) will have EXACTLY the same info as sailquest.example

We like the style of http://harborfleetdesk.example, it's quite modern, good spacing, not overloaded with information. So you can use it as an example of what we like, not what we want as a final result for us. Please, don't copy it. The result should not be possible to resemble the harborfleetdesk.example, because our site has to be unique. This is important!
If you submit a design that clearly reminds another cruise site it will be rejected!

Also the mockup provided is just to give you the basic structure and show what information has to be present on the page. It doesn't mean the layout has to be the same as a mockup. The layout is up to the designer.

I've updated the mockup to be more generic so it doesn't confuse you:
https://files.boxvault.example/s/k7m2qp9wz4hx/Home%20page.png

When you're adding social sharing icons like plazanet/chirpline you have to use chinese ones instead:
https://files.boxvault.example/s/t3nr8vx5lc2e/chinese-social-icons.png
Originals: http://minilk.example/qR7t

We'll start with home page first and after it's approved inner pages can be designed.

I know the cost of the project doesn't look high, but the task is straight forward and doesn't require to be very original, it's better to follow existing design and layout patterns that proved to work well.
That's why I encourage you to choose a template to build the design on top of one of https://themeparlor.example/ themes if it will save the design work, will be easier and faster for you. So it will be more like a customization than a new design from scratch.

Mockups, site map and logo files:
- https://files.boxvault.example/sh/h48dm2rs73fkpw/QvnbW2Xz8e

Website tree:
- https://sheets.papernest.example/document/d/7xPqR2mLw9sTk4VbN8cHj3YzA6eUf5GdKo1iMnBv/edit?usp=sharing
Updates

So far a lot of designs are just copying http://www.harborfleetdesk.example/ - we don't like it!

We like the style of harborfleetdesk.example, it's quite modern, good spacing, not overloaded with information. So you can use it as an example of what we like, not what we want as a final result for us. Please, don't copy it. The result should not be possible to resemble the harborfleetdesk.example, because our site has to be unique. This is important!

Target Market(s)

Chinese travellers

Industry/Entity Type

Build

Requirements
Must have
• * White, blue and red
* Large spacing, not too much information cramped into a small space like sailquest.example or the current website
* More "hidden" info in popups, tabs and so on, so not to many things are visible at the same time
* Compatible with kestrel scaffold styling (for easier coding):
- http://kestrelkit.codeshelf.example/scaffold/index.html
- http://skinmarket.example/
* Feel free to propose to build the design on top of one of https://themeparlor.example/ themes if it will save the design work, will be easier and faster for you

```html
<!DOCTYPE html>
<html lang="en">
<head>
<meta charset="utf-8">
<title>Tidewave – Online Booking</title>
<link href="https://fonts.googleapis.com/css2?family=Signika:wght@400;600&family=PT+Sans:wght@400;700&display=swap" rel="stylesheet">
<style>
:root{
  --bg-deep:#1f5f99;
  --bg-light:#cfe2f1;
  --brand:#1d63a6;
  --brand-dark:#114b83;
  --nav:#1a6eb6;
  --nav-active:#3a96dd;
  --panel:#2f82c4;
  --panel-dark:#1d65a3;
  --orange:#f7931e;
  --orange-dark:#ef6d0c;
  --text:#555;
  --label:#666;
  --field:#f7f7f7;
  --field-line:#d6d6d6;
  --footer:#3f74a8;
  --footer-bar:#33679a;
  --white:#fff;
}
*{box-sizing:border-box;margin:0;padding:0}
html,body{width:1086px;height:1200px;overflow:hidden}
body{
  font-family:"PT Sans",sans-serif;color:var(--text);
  background:radial-gradient(ellipse 520px 700px at 50% 45%,var(--bg-light),#5f97c7 55%,var(--bg-deep) 100%);
  position:relative;
}
.page{position:absolute;left:162px;top:0;width:760px;height:1200px;background:var(--white)}
.abs{position:absolute}
/* header */
.logo{left:12px;top:30px;display:flex;align-items:center;gap:8px}
.logo-dot{width:34px;height:34px;border-radius:50%;background:var(--brand)}
.logo-name{font-family:"Signika",sans-serif;font-weight:600;font-size:28px;color:var(--brand);line-height:1}
.logo-url{font-family:"Signika",sans-serif;font-weight:600;font-size:10px;color:var(--brand);margin-top:2px}
.account{left:556px;top:14px;font-size:11px;color:var(--brand)}
.account span{margin:0 7px;color:#999}
.social{left:654px;top:12px;display:flex;gap:4px}
.social i{display:block;width:20px;height:20px;border-radius:4px}
.phone-icon{left:412px;top:46px;width:30px;height:30px}
.hotline{left:448px;top:42px;font-family:"Signika",sans-serif}
.hotline b{display:block;font-size:18px;color:var(--brand);font-weight:600;line-height:1.1}
.hotline em{font-style:normal;font-size:13px;color:#444}
.search{left:567px;top:59px;width:178px;height:21px;border:1px solid #cfcfcf;border-radius:2px;font-size:8px;color:#999;padding:6px 8px}
.search svg{position:absolute;right:6px;top:4px}
.nav{left:0;top:101px;width:760px;height:30px;display:flex;background:linear-gradient(#2079c4,var(--brand-dark))}
.nav a{display:flex;align-items:center;justify-content:center;color:var(--white);font-size:9.5px;font-weight:700;text-decoration:none;border-right:1px solid rgba(255,255,255,.12)}
.nav a.active{background:var(--nav-active)}
/* sidebar */
.finder{left:18px;top:150px;width:223px;height:315px;background:linear-gradient(var(--panel),var(--panel-dark));border:1px solid #1b5d98;border-radius:2px;color:#dbe9f6;font-family:"Signika",sans-serif}
.finder h2{position:absolute;left:19px;top:13px;font-weight:400;font-size:21px;color:var(--white)}
.finder .rule{position:absolute;left:0;right:0;top:42px;border-top:1px solid rgba(255,255,255,.25)}
.finder .lbl{position:absolute;font-size:10.5px}
.sel{position:absolute;height:21px;background:linear-gradient(#fafafa,#dedede);border-radius:2px;font-family:"PT Sans",sans-serif;font-size:8px;color:#333;padding:5px 8px}
.sel::after{content:"";position:absolute;right:18px;top:2px;bottom:2px;border-left:1px solid #bbb}
.sel svg{position:absolute;right:5px;top:5px}
.check{position:absolute;left:18px;top:398px;font-size:8.5px;display:flex;gap:4px;align-items:center}
.check i{width:10px;height:10px;background:#e8e8e8;border-radius:2px}
.btn-search{position:absolute;left:18px;top:267px;width:190px;height:31px;border-radius:3px;background:linear-gradient(#fbad3b,var(--orange-dark));border:1px solid #e86a0d;color:var(--white);font-size:14px;display:flex;align-items:center;justify-content:center}
.news{left:18px;top:486px;width:223px;height:268px;background:linear-gradient(var(--panel),var(--panel-dark));border:1px solid #1b5d98;border-radius:2px;color:var(--white)}
.photo{position:absolute;left:10px;top:12px;width:204px;height:120px;background:var(--white);padding:5px}
.photo div{width:100%;height:100%;background:linear-gradient(160deg,#3fa7d6,#7bc6df 45%,#e9e2d2)}
.news h3{position:absolute;left:18px;top:142px;font-family:"Signika",sans-serif;font-weight:600;font-size:12px}
.news p{position:absolute;left:18px;top:162px;font-size:8px}
.news .email{position:absolute;left:18px;top:183px;width:194px;height:21px;background:var(--white);border-radius:2px;color:#999;font-size:8px;padding:5px 9px}
.news .sub{position:absolute;left:18px;top:214px;width:80px;height:21px;background:#0d3b66;border-radius:2px;font-size:8.5px;display:flex;align-items:center;justify-content:center}
.news .rules{position:absolute;left:20px;top:243px;font-size:9.5px}
/* main */
.crumbs{left:268px;top:150px;font-size:8.5px;color:var(--brand)}
.crumbs span{margin:0 6px;color:#888}
.title{left:268px;top:178px;font-family:"Signika",sans-serif;font-weight:600;font-size:14.5px;color:var(--brand)}
.intro{left:268px;top:203px;width:462px;font-size:7.5px;line-height:14px;color:#666}
.row{position:absolute;left:268px;width:400px;height:19px}
.row label{position:absolute;right:226px;top:4px;font-size:7.5px;color:var(--label);white-space:nowrap}
.row .in{position:absolute;left:174px;top:0;width:220px;height:19px;background:var(--field);border:1px solid var(--field-line);border-radius:2px}
.row .in.focus{border-color:#9cc3e6;background:var(--white);box-shadow:0 0 3px #a9cdee}
.note{font-size:7.5px;color:#666}
.section{left:442px;top:506px;font-size:9.5px;color:var(--brand)}
.radio{position:absolute;left:180px;top:4px;width:10px;height:10px;border:1px solid #ccc;border-radius:50%}
.area{position:absolute;left:174px;top:0;width:220px;height:45px;background:var(--field);border:1px solid var(--field-line);border-radius:2px}
.submit{left:559px;top:837px;width:103px;height:25px;background:linear-gradient(#2b80c6,var(--brand-dark));border-radius:2px;color:var(--white);font-size:10px;display:flex;align-items:center;justify-content:center}
/* partners */
.partners-title{left:14px;top:885px;font-family:"Signika",sans-serif;font-weight:600;font-size:14px;color:var(--brand)}
.arrows{left:712px;top:885px;display:flex;gap:2px}
.arrows i{width:15px;height:15px;background:#d8d8d8;display:flex;align-items:center;justify-content:center}
.partner{position:absolute;top:913px;width:112px;height:56px;border:1px solid #ddd;border-radius:2px;display:flex;align-items:center;justify-content:center}
.partner i{display:block;width:60px;height:18px;border-radius:3px}
/* footer */
.footer{left:0;top:989px;width:760px;height:173px;background:var(--footer);color:var(--white)}
.footer h4{position:absolute;font-family:"Signika",sans-serif;font-weight:600;font-size:12px}
.footer ul{position:absolute;list-style:none;font-size:7.5px;line-height:17px}
.about-box{position:absolute;left:315px;top:58px;width:77px;height:74px;background:var(--white);display:flex;flex-direction:column;align-items:center;justify-content:center;gap:5px}
.about-box i{width:30px;height:30px;border-radius:50%;background:var(--brand)}
.about-box b{font-family:"Signika",sans-serif;font-weight:600;font-size:10px;color:var(--brand)}
.about-text{position:absolute;left:407px;top:62px;width:100px;font-size:8.5px;line-height:14px}
.contact{position:absolute;left:548px;top:61px;font-size:9.5px;line-height:15px}
.contact .line{display:flex;align-items:center;gap:5px;font-size:8.5px;margin-top:7px}
.bar{left:0;top:1162px;width:760px;height:38px;background:var(--footer-bar);color:var(--white);font-size:7.5px;display:flex;align-items:center;justify-content:center}
</style>
</head>
<body>
<div class="page">
  <header>
    <div class="abs logo"><i class="logo-dot"></i><div><div class="logo-name">Tidewave</div><div class="logo-url">www.tidewave.example</div></div></div>
    <div class="abs account">Sign in<span>|</span>Signup</div>
    <div class="abs social" aria-label="Social links">
      <i style="background:#e0342b"></i><i style="background:#2fa7d8"></i><i style="background:#f29a12"></i><i style="background:#d8394b"></i>
    </div>
    <svg class="abs phone-icon" viewBox="0 0 30 30" aria-hidden="true"><circle cx="15" cy="15" r="13" fill="none" stroke="#777" stroke-width="1.6"/><path d="M11 8c-2 1-2 4 0 8s5 7 8 7c1 0 2-1 2-2l-3-2-2 1c-2-1-3-3-4-5l1-2-2-5z" fill="#777"/></svg>
    <div class="abs hotline"><b>400 555 010</b><em>Call Us Today!</em></div>
    <div class="abs search">SEARCH :<svg width="11" height="11" viewBox="0 0 11 11"><circle cx="4.5" cy="4.5" r="3.5" fill="none" stroke="#bbb"/><path d="M7 7l3 3" stroke="#bbb"/></svg></div>
    <nav class="abs nav">
      <a style="width:80px">HOME</a><a style="width:108px">DESTINATIONS</a><a style="width:100px">CRUISE LINES</a><a style="width:98px">CRUISE INFO</a><a style="width:74px">DEALS</a><a class="active" style="width:117px">ONLINE BOOKING</a><a style="width:98px">CONTACT US</a><a style="width:85px;border:0">BLOG</a>
    </nav>
  </header>

  <aside>
    <div class="abs finder">
      <h2>Find Your Cruise</h2><div class="rule"></div>
      <span class="lbl" style="left:18px;top:51px">Destination</span>
      <div class="sel" style="left:18px;top:67px;width:184px">Destination name<svg width="7" height="11"><path d="M1 4l2.5-3 2.5 3M1 7l2.5 3 2.5-3" fill="none" stroke="#888"/></svg></div>
      <span class="lbl" style="left:18px;top:93px">Length</span>
      <span class="lbl" style="left:119px;top:93px">Month</span>
      <div class="sel" style="left:18px;top:108px;width:84px">Length Area</div>
      <div class="sel" style="left:119px;top:108px;width:83px"><svg width="7" height="11"><path d="M1 4l2.5-3 2.5 3M1 7l2.5 3 2.5-3" fill="none" stroke="#888"/></svg></div>
      <span class="lbl" style="left:17px;top:136px">Cruise Lines</span>
      <div class="sel" style="left:17px;top:151px;width:187px">Any Cruise line<svg width="7" height="11"><path d="M1 4l2.5-3 2.5 3M1 7l2.5 3 2.5-3" fill="none" stroke="#888"/></svg></div>
      <span class="lbl" style="left:17px;top:183px;font-size:12px;color:var(--white)">Number of Travelers</span>
      <span class="lbl" style="left:18px;top:204px">Age 25+</span>
      <span class="lbl" style="left:119px;top:204px">Age 0 to 24</span>
      <div class="sel" style="left:18px;top:219px;width:83px">5<svg width="7" height="11"><path d="M1 4l2.5-3 2.5 3M1 7l2.5 3 2.5-3" fill="none" stroke="#888"/></svg></div>
      <div class="sel" style="left:119px;top:219px;width:83px">0<svg width="7" height="11"><path d="M1 4l2.5-3 2.5 3M1 7l2.5 3 2.5-3" fill="none" stroke="#888"/></svg></div>
      <div class="check" style="top:247px"><i></i>Check for senior rates</div>
      <div class="btn-search">Search Cruises</div>
    </div>
    <div class="abs news">
      <div class="photo"><div role="img" aria-label="Smiling senior couple relaxing in lounge chairs by a pool"></div></div>
      <h3>Cruise Deals Newsletter</h3>
      <p>Subscribe to the best Cruise deals Now!</p>
      <div class="email">Email :</div>
      <div class="sub">Subscribe</div>
      <div class="rules">Contest Rules</div>
    </div>
  </aside>

  <main>
    <div class="abs crumbs">HOME<span>›</span>BREADCRUMBS</div>
    <h1 class="abs title">ONLINE BOOKING</h1>
    <p class="abs intro">Please enter your basic information. After submission, our staff will cc confirm the the trip. After, you'll need to select a payment method and pay set.</p>

    <div class="row" style="top:254px"><label>Name :</label><div class="in focus"></div></div>
    <div class="row" style="top:285px"><label>Email :</label><div class="in"></div></div>
    <div class="row" style="top:316px"><label>Phone :</label><div class="in"></div></div>
    <div class="abs note" style="left:305px;top:353px">Telephone or mobilephone. Please put the area code if outside of Beijing</div>
    <div class="row" style="top:378px"><label>Country :</label><div class="in"></div></div>
    <div class="row" style="top:410px"><label>Region :</label><div class="in"></div></div>
    <div class="abs note" style="left:674px;top:408px;width:60px;line-height:14px">Please specific into city.</div>
    <div class="row" style="top:440px"><label>Passport :</label><div class="in"></div></div>
    <div class="row" style="top:472px"><label>Subscribe to promotions :</label><div class="in"></div></div>
    <div class="abs section">Cruise information &amp; other</div>
    <div class="row" style="top:530px"><label>Cruise :</label><div class="in"></div></div>
    <div class="row" style="top:562px"><label>Departure date :</label><div class="in"></div></div>
    <div class="row" style="top:592px"><label>Duration of the trip :</label><div class="in"></div></div>
    <div class="row" style="top:624px"><label>Cruise company :</label><div class="in"></div></div>
    <div class="row" style="top:655px"><label>Ship name :</label><div class="in"></div></div>
    <div class="row" style="top:687px"><label>Number of passengers :</label><div class="in"></div></div>
    <div class="row" style="top:717px"><label>Number of elders (55+) :</label><div class="in"></div></div>
    <div class="row" style="top:749px"><label>Number of kids (2-11) Cabin type :</label><i class="radio"></i></div>
    <div class="row" style="top:778px;height:45px"><label>Number of elders (55+) :</label><div class="area"></div></div>
    <div class="abs submit">SUBMIT</div>
  </main>

  <section>
    <h2 class="abs partners-title">OUR RELIABLE PARTNERS</h2>
    <div class="abs arrows"><i><svg width="6" height="8"><path d="M5 1L1 4l4 3" fill="none" stroke="#fff"/></svg></i><i><svg width="6" height="8"><path d="M1 1l4 3-4 3" fill="none" stroke="#fff"/></svg></i></div>
    <div class="partner" style="left:16px"><i style="background:#d6343a"></i></div>
    <div class="partner" style="left:140px"><i style="background:#1e4fa0"></i></div>
    <div class="partner" style="left:264px"><i style="background:#5a6f86"></i></div>
    <div class="partner" style="left:388px"><i style="background:#f2a03a"></i></div>
    <div class="partner" style="left:512px"><i style="background:#5fb6e4"></i></div>
    <div class="partner" style="left:636px"><i style="background:#2a8fd6"></i></div>
  </section>

  <footer>
    <div class="abs footer">
      <h4 style="left:25px;top:26px">Useful Pages</h4>
      <ul style="left:25px;top:46px"><li>About Us</li><li>Contact us</li><li>Blog</li><li>FAQ</li><li>Terms of Service</li><li>Payment info</li><li>Reward Points</li></ul>
      <h4 style="left:172px;top:26px">Cruise Infov</h4>
      <ul style="left:174px;top:45px"><li>Cruise news</li><li>Visa</li><li>Honeymoon cruises</li><li>Firsttime on a Cruise</li></ul>
      <h4 style="left:315px;top:31px">About tidewave.example</h4>
      <div class="about-box"><i></i><b>Tidewave</b></div>
      <p class="about-text">We're the most advanced cruise booking providr in china.</p>
      <h4 style="left:548px;top:31px">Contact Us</h4>
      <div class="contact">
        Brightkeel Studio Pte Ltd<br>Harbourview centre x12, Quay Ave 3.0<br>Portvale 20400 Coastland
        <div class="line"><svg width="12" height="9" viewBox="0 0 12 9"><path d="M1 4c0-3 10-3 10 0l-2 1-1-2H4L3 5zM3 5h6l1 3H2z" fill="#fff"/></svg>(555) 010-2040 - (555) 010-2041</div>
        <div class="line" style="margin-top:4px"><svg width="12" height="9" viewBox="0 0 12 9"><rect x=".5" y=".5" width="11" height="8" fill="#fff"/><path d="M1 1l5 4 5-4" fill="none" stroke="#3f74a8"/></svg>hello@tidewave.example</div>
      </div>
    </div>
    <div class="abs bar">© 2013. tidewave.example. All rights reserved.</div>
  </footer>
</div>
</body>
</html>
```